The Linen Loft Co

We need a business card design for our wardrobe company.
Please visit our website www.gentlelinenlofts.com to get an idea of who we are.

```html
<!DOCTYPE html>
<html lang="en">
<head>
<meta charset="utf-8">
<title>The Linen Loft Co — Business Card</title>
<link href="https://fonts.googleapis.com/css2?family=Montserrat:wght@500&family=Lato:wght@400;700&display=swap" rel="stylesheet">
<style>
  :root {
    --backdrop: #5f5f5f;
    --card: #171717;
    --gold: #9c8358;
    --ink: #f2f2f2;
  }
  * { margin: 0; padding: 0; box-sizing: border-box; }
  html, body { width: 1200px; height: 1200px; overflow: hidden; }
  body { background: var(--backdrop); position: relative; }

  .business-card {
    position: absolute;
    left: 100px; top: 309px;
    width: 1000px; height: 582px;
    background: var(--card);
  }

  .brand-mark {
    position: absolute;
    left: 207px; top: 118px;
    width: 127px; height: 127px;
    border: 6px solid var(--gold);
  }
  .brand-name {
    position: absolute;
    left: 410px; top: 128px;
    font-family: "Montserrat", sans-serif;
    font-weight: 500;
    font-size: 40px;
    letter-spacing: 1px;
    color: var(--gold);
    text-transform: uppercase;
    white-space: nowrap;
  }
  .brand-tagline {
    position: absolute;
    left: 450px; top: 184px;
    font-family: "Montserrat", sans-serif;
    font-weight: 500;
    font-size: 31px;
    color: var(--gold);
    white-space: nowrap;
  }

  .person {
    position: absolute;
    right: 532px; top: 356px;
    text-align: right;
    font-family: "Lato", sans-serif;
    color: var(--ink);
  }
  .person-name {
    font-weight: 700;
    font-size: 31px;
    color: var(--gold);
    line-height: 36px;
  }
  .person-role {
    font-weight: 700;
    font-size: 25px;
    line-height: 30px;
    margin-top: 8px;
  }
  .person-address {
    font-size: 24px;
    line-height: 28px;
    margin-top: 14px;
    letter-spacing: 0.5px;
  }

  .divider {
    position: absolute;
    left: 500px; top: 352px;
    width: 2px; height: 143px;
    background: var(--gold);
  }

  .contact-list {
    position: absolute;
    left: 540px; top: 356px;
    list-style: none;
    font-family: "Lato", sans-serif;
    font-size: 24px;
    color: var(--ink);
    letter-spacing: 0.4px;
  }
  .contact-item {
    display: flex;
    align-items: center;
    height: 34.5px;
  }
  .contact-icon {
    width: 16px; height: 16px;
    margin-right: 12px;
    fill: var(--gold);
    flex: none;
  }
</style>
</head>
<body>
  <main class="business-card">
    <div class="brand-mark" aria-hidden="true"></div>
    <div class="brand-name">The Linen Loft Co</div>
    <div class="brand-tagline">Crafted for Calm Spaces</div>

    <div class="person">
      <div class="person-name">Dara Quinlan</div>
      <div class="person-role">Manager</div>
      <div class="person-address">14-16 Marlowe Orchard<br>Street 208531, USA</div>
    </div>

    <div class="divider"></div>

    <ul class="contact-list">
      <li class="contact-item">
        <svg class="contact-icon" viewBox="0 0 16 16" aria-hidden="true"><path d="M3.2 1.5l2.4 2.6-1.3 1.8c.9 2.1 2.5 3.7 4.6 4.6l1.8-1.3 2.6 2.4-1.4 2.4C6.4 13.6 2.4 9.6 1 4.1z"/></svg>
        555-210-3391
      </li>
      <li class="contact-item">
        <svg class="contact-icon" viewBox="0 0 16 16" aria-hidden="true"><path d="M4.5 1h7v14h-7zM5.7 2.5v10h4.6v-10z"/></svg>
        555-738-0264
      </li>
      <li class="contact-item">
        <svg class="contact-icon" viewBox="0 0 16 16" aria-hidden="true"><path d="M1 3.5h14v9H1zM2 4.5l6 4.3 6-4.3z" fill-rule="evenodd"/></svg>
        hello@gentlelinenlofts.com
      </li>
      <li class="contact-item">
        <svg class="contact-icon" viewBox="0 0 16 16" aria-hidden="true"><circle cx="8" cy="8" r="6.5"/></svg>
        www.gentlelinenlofts.com
      </li>
    </ul>
  </main>
</body>
</html>
```